Tellmora Corporate Stationery

Look for design of all new corporate stationery for an existing insurance broking business that is going through a redesign and move from older partners to younger family members. New Logo is attached. Company is Brisbane based.
Colours in the Logo is Hex #43bed8 and website features a lot of hex #17b8d8. Website front page "A plan to protect you" - headline. "Professional and Individual advice to protect your greatest assets" - tagline.

Stationery required: Business Cards, Letter head, Thank-you cards, Birthday cards, Presentation folders, With Compliment slips and a powerpoint template. We also would like to send a card to all customers with the something along of the lines of "something new".

Target Market(s)

Customers of Insurance business looking at superannuation, life and income protection insurance, investment advice and wills

Industry/Entity Type

Insurance Broker

Font styles to use
Other font styles liked:
• same as logo

Requirements
Must have
• The above designs for new stationery for the new business including:
• Business Cards, Letter head, Thank-you cards, Birthday cards, Presentation folders, With Compliment slips and a powerpoint template. We also would like to send a card to all customers with the something along of the lines of "something new".
Nice to have
• It is a new look - long time family business being passed to next generation - big focus on advice for YOU, individual advice etc..

```html
<!DOCTYPE html>
<html lang="en">
<head>
<meta charset="utf-8">
<title>Tellmora Business Card</title>
<link rel="stylesheet" href="https://fonts.googleapis.com/css2?family=Open+Sans:ital,wght@0,400;0,600;1,400&display=swap">
<style>
  :root {
    --backdrop: #2b2b2d;
    --card-white: #ffffff;
    --brand-cyan: #3fc0d8;
    --brand-grey: #7b7b7e;
    --text-dark: #4a4a4d;
    --rule: #8a8a8d;
  }
  * { box-sizing: border-box; margin: 0; padding: 0; }
  html, body {
    width: 1200px; height: 987px; overflow: hidden;
    background: var(--backdrop);
    font-family: "Open Sans", Arial, sans-serif;
  }
  .card {
    position: absolute; left: 293px; width: 615px; height: 350px;
    overflow: hidden;
  }
  .card-front { top: 130px; background: var(--card-white); }
  .card-back { top: 505px; background: var(--brand-cyan); }

  /* front */
  .brand {
    position: absolute; left: 0; right: 0; top: 58px;
    display: flex; align-items: center; justify-content: center; gap: 16px;
  }
  .brand-dot {
    width: 44px; height: 44px; border-radius: 50%;
    background: var(--brand-cyan);
  }
  .brand-name {
    font-size: 46px; font-weight: 600; color: var(--brand-cyan);
    letter-spacing: 1px; line-height: 1;
  }
  .divider {
    position: absolute; left: 36px; right: 40px; top: 213px;
    height: 1px; background: var(--rule);
  }
  .contact-list {
    position: absolute; left: 37px; top: 226px; list-style: none;
  }
  .contact-list li {
    display: flex; align-items: center; gap: 7px;
    height: 24px; font-size: 15.5px; color: var(--text-dark);
  }
  .contact-list svg { width: 14px; height: 14px; fill: var(--brand-cyan); flex: none; }
  .person {
    position: absolute; right: 40px; top: 220px; text-align: right;
    color: var(--text-dark); font-size: 15.5px; line-height: 24px;
  }
  .person-name {
    font-size: 21px; font-weight: 600; color: var(--brand-cyan);
    line-height: 28px; letter-spacing: 0.3px;
  }
  .person-title { color: var(--brand-grey); }
  .base-band { position: absolute; left: 0; bottom: 0; width: 100%; height: 11px; }

  /* back */
  .back-brand {
    position: absolute; right: 29px; top: 248px; text-align: right; color: var(--card-white);
  }
  .back-name {
    display: flex; align-items: center; justify-content: flex-end; gap: 10px;
    font-size: 36px; font-weight: 600; letter-spacing: 1px; line-height: 1;
  }
  .back-dot { width: 26px; height: 26px; border-radius: 50%; background: var(--card-white); }
  .back-web {
    margin-top: 14px; font-size: 15px; font-style: italic; letter-spacing: 4px;
  }
</style>
</head>
<body>
  <section class="card card-front">
    <div class="brand">
      <span class="brand-dot"></span>
      <span class="brand-name">Tellmora</span>
    </div>
    <div class="divider"></div>
    <ul class="contact-list">
      <li>
        <svg viewBox="0 0 16 16" aria-hidden="true"><path d="M3.6 1.2 6 3.6 4.7 5.6c.9 2 2.6 3.7 4.7 4.7l2-1.3 2.4 2.4-1.6 2.4C7 13.6 2.4 9 1.2 2.8z"/></svg>
        614 208 3391
      </li>
      <li>
        <svg viewBox="0 0 16 16" aria-hidden="true"><path d="M4.5 0h7A1.5 1.5 0 0 1 13 1.5v13a1.5 1.5 0 0 1-1.5 1.5h-7A1.5 1.5 0 0 1 3 14.5v-13A1.5 1.5 0 0 1 4.5 0zM5 2v10h6V2zm3 11a1 1 0 1 0 0 2 1 1 0 0 0 0-2z"/></svg>
        614 775 0182
      </li>
      <li>
        <svg viewBox="0 0 16 16" aria-hidden="true"><path d="M4 1h8v4H4zM1 6h14v7h-2v-2H3v2H1zm3 6h8v3H4z"/></svg>
        614 502 6647
      </li>
      <li>
        <svg viewBox="0 0 16 16" aria-hidden="true"><path d="M1 3h14v10H1zm1.2 1.2v.4L8 8.8l5.8-4.2v-.4z"/></svg>
        hello@tellmora.com
      </li>
    </ul>
    <div class="person">
      <div class="person-name">DANIEL HART</div>
      <div class="person-title">CEO/FOUNDER</div>
      <div>42 Wattle Grove</div>
      <div>Brisbane, QLD 4000</div>
    </div>
    <svg class="base-band" viewBox="0 0 615 11" preserveAspectRatio="none" aria-hidden="true">
      <polygon points="0,0 401,0 398,11 0,11" fill="var(--brand-cyan)"/>
      <polygon points="404,0 615,0 615,11 401,11" fill="var(--brand-grey)"/>
    </svg>
  </section>

  <section class="card card-back">
    <div class="back-brand">
      <div class="back-name"><span class="back-dot"></span>TELLMORA</div>
      <div class="back-web">www.tellmora.com</div>
    </div>
  </section>
</body>
</html>
```